Business Card Design for Occupational Medicine Start Up Company

We need to design a professional business card. We are a healthcare company providing occupational medicine services to blue collar industries. We are professional, efficient and high quality service providers.

Target Market(s)

Blue Collar Industry: Shipbuilding, Ports, Trucking Companies; The Executives and Safety Officers for these companies

Industry/Entity Type

Healthcare

Contact Information for Business Card

Logo, Name, Title, Email, Phone

Other font styles liked:
• Please match our Brand Guide

Requirements
Must have
• Our Company Colors and Logo

```html
<!DOCTYPE html>
<html lang="en">
<head>
<meta charset="utf-8">
<title>ShiftWell Clinics – Business Card</title>
<link rel="stylesheet" href="https://fonts.googleapis.com/css2?family=Montserrat:wght@400;500;600;700&display=swap">
<style>
  :root {
    --bg: #2a2a2a;
    --card: #f4f4f2;
    --navy: #2e3179;
    --sky: #2c9fd8;
    --sky-soft: #d6e9f5;
    --amber: #f2ab3c;
    --ink: #2e3179;
  }
  html, body {
    margin: 0;
    padding: 0;
    width: 1200px;
    height: 1200px;
    overflow: hidden;
    background: var(--bg);
    font-family: "Montserrat", sans-serif;
  }
  .card {
    position: absolute;
    left: 303px;
    width: 594px;
    height: 348px;
    border-radius: 22px;
    background: var(--card);
    color: var(--ink);
    overflow: hidden;
  }
  .card--front { top: 200px; }
  .card--back { top: 637px; }

  /* Front */
  .front-mark {
    position: absolute;
    left: 50%;
    top: 80px;
    width: 80px;
    height: 80px;
    margin-left: -40px;
    border-radius: 50%;
    background: var(--navy);
  }
  .front-name {
    position: absolute;
    left: 0;
    right: 0;
    top: 180px;
    text-align: center;
    font-weight: 600;
    color: var(--navy);
    line-height: 1;
  }
  .front-name .brand { display: block; font-size: 36px; letter-spacing: 0.5px; }
  .front-name .brand-sub { display: block; font-size: 17px; letter-spacing: 5px; margin-top: 8px; }
  .front-url {
    position: absolute;
    left: 0;
    right: 0;
    top: 300px;
    text-align: center;
    font-size: 15px;
    letter-spacing: 1px;
    color: var(--navy);
  }
  .front-url .url-name { color: var(--sky); }
  .front-url .url-accent { color: var(--amber); }

  /* Back */
  .back-name {
    position: absolute;
    left: 25px;
    top: 42px;
    font-weight: 600;
    color: var(--navy);
    line-height: 1;
    text-align: center;
  }
  .back-name .brand { display: block; font-size: 23px; letter-spacing: 0.3px; }
  .back-name .brand-sub { display: block; font-size: 12px; letter-spacing: 3.5px; margin-top: 5px; }
  .person {
    position: absolute;
    left: 25px;
    top: 138px;
  }
  .person-name {
    margin: 0;
    font-size: 25px;
    font-weight: 500;
    color: var(--sky);
    letter-spacing: 0.5px;
  }
  .person-title {
    margin: 4px 0 0;
    font-size: 15px;
    color: var(--navy);
  }
  .address {
    position: absolute;
    left: 25px;
    top: 208px;
    margin: 0;
    font-style: normal;
    font-size: 15px;
    line-height: 21px;
    color: var(--navy);
  }
  .contacts {
    position: absolute;
    left: 25px;
    top: 260px;
    margin: 0;
    padding: 0;
    list-style: none;
    font-size: 15px;
    color: var(--navy);
  }
  .contacts li {
    display: flex;
    align-items: center;
    height: 21px;
  }
  .contacts svg {
    width: 13px;
    height: 13px;
    margin-right: 15px;
    flex: none;
  }

  /* Large brand area on the back */
  .brand-feature {
    position: absolute;
    left: 300px;
    top: 14px;
    width: 280px;
    height: 320px;
  }
  .brand-feature-disc {
    position: absolute;
    left: 30px;
    top: 0;
    width: 220px;
    height: 220px;
    border-radius: 50%;
    background: var(--sky-soft);
  }
  .brand-feature-name {
    position: absolute;
    left: 0;
    right: 0;
    top: 248px;
    text-align: center;
    font-size: 34px;
    font-weight: 600;
    letter-spacing: 0.5px;
    color: var(--navy);
  }
</style>
</head>
<body>

<section class="card card--front">
  <div class="front-mark"></div>
  <div class="front-name">
    <span class="brand">SHIFTWELL</span>
    <span class="brand-sub">CLINICS</span>
  </div>
  <div class="front-url">www.<span class="url-name">shiftwell</span><span class="url-accent">clinics</span>.com</div>
</section>

<section class="card card--back">
  <div class="back-name">
    <span class="brand">SHIFTWELL</span>
    <span class="brand-sub">CLINICS</span>
  </div>

  <div class="person">
    <p class="person-name">DANIEL MARSH</p>
    <p class="person-title">Senior Doctor</p>
  </div>

  <address class="address">
    48 Harbor Lane, Suite 210<br>
    Port Elm, State 40210
  </address>

  <ul class="contacts">
    <li>
      <svg viewBox="0 0 16 16" aria-hidden="true"><path fill="#2c9fd8" d="M3 2h3l1.5 3.5-2 1.3a9 9 0 0 0 3.7 3.7l1.3-2L14 10v3a1 1 0 0 1-1 1A12 12 0 0 1 2 3a1 1 0 0 1 1-1z"/></svg>
      555-018-2740
    </li>
    <li>
      <svg viewBox="0 0 16 16" aria-hidden="true"><rect x="1" y="3" width="14" height="10" fill="#2e3179"/><path d="M1 3l7 6 7-6" fill="none" stroke="#f4f4f2" stroke-width="1.4"/></svg>
      daniel@shiftwell.com
    </li>
    <li>
      <svg viewBox="0 0 16 16" aria-hidden="true"><circle cx="8" cy="8" r="6.5" fill="none" stroke="#f2ab3c" stroke-width="1.5"/><path d="M1.5 8h13M8 1.5c-3 3.5-3 9.5 0 13M8 1.5c3 3.5 3 9.5 0 13" fill="none" stroke="#f2ab3c" stroke-width="1.2"/></svg>
      www.shiftwell.com
    </li>
  </ul>

  <div class="brand-feature" role="img" aria-label="Large ShiftWell Clinics brand area">
    <div class="brand-feature-disc"></div>
    <div class="brand-feature-name">SHIFTWELL</div>
  </div>
</section>

</body>
</html>
```